Request for Business Card Design

Hi. My name is Marlene, I am looking for a new business card design for my company, Quarrow Signal Instruments, LLC. I really like the design you did for Tarsel Venture and was hoping you could do something similar using our full logo and our mark. I am also open to any raised texture design using our mark. I have attached our full logo, which would need to be somewhere on the card, as well as the mark in both outline and full form, as well as our brand colors / guide. The card does not have to be white, as long as our logo and mark appear. I actually like darker colored business cards more, but am open to all options. If you are interested in working with me, please let me know. We would also take the business card design into letterhead design if you can do that.

```html
<!DOCTYPE html>
<html lang="en">
<head>
<meta charset="utf-8">
<title>Quarrow Signal Instruments — Business Card</title>
<link rel="stylesheet" href="https://fonts.googleapis.com/css2?family=Open+Sans:wght@400;600;700&display=swap">
<style>
  :root {
    --backdrop: #dcdcda;
    --card-light: #ffffff;
    --card-dark: #3c3c3e;
    --accent: #1a9bc7;
    --ink: #3a3a3c;
    --ink-soft: #6b6b6e;
    --paper-text: #ffffff;
  }
  * { margin: 0; padding: 0; box-sizing: border-box; }
  html, body {
    width: 1200px; height: 801px; overflow: hidden;
    background: var(--backdrop);
    font-family: "Open Sans", Arial, sans-serif;
  }
  .stage {
    position: relative; width: 1200px; height: 801px;
    display: flex; align-items: center; justify-content: center; gap: 40px;
  }
  .card {
    position: relative; width: 540px; height: 309px;
    border-bottom: 4px solid var(--accent);
    overflow: hidden;
  }
  .card--front { background: var(--card-light); }
  .card--back { background: var(--card-dark); }

  .brand {
    position: absolute; left: 36px; top: 140px;
    display: flex; align-items: center; gap: 14px;
  }
  .brand__dot {
    width: 34px; height: 34px; border-radius: 50%;
    background: var(--accent); flex: none;
  }
  .brand__name {
    color: var(--ink); font-weight: 700; line-height: 1;
  }
  .brand__name .main { display: block; font-size: 34px; letter-spacing: 3px; }
  .brand__name .sub { display: block; font-size: 9.5px; letter-spacing: 0.6px; margin-top: 5px; }

  .divider {
    position: absolute; left: 300px; top: 44px; width: 1.5px; height: 214px;
    background: var(--accent);
  }
  .contact {
    position: absolute; left: 320px; top: 48px; color: var(--ink-soft);
    font-size: 12.5px; line-height: 1.5;
  }
  .contact__name {
    color: var(--accent); font-weight: 700; font-size: 17px; letter-spacing: 0.5px;
  }
  .contact__title { margin-bottom: 18px; }
  .contact__address { margin-bottom: 16px; }
  .contact__line { display: flex; align-items: center; gap: 8px; }
  .contact__line svg { width: 11px; height: 11px; flex: none; fill: var(--accent); }

  .back-brand {
    position: absolute; left: 34px; bottom: 30px;
    color: var(--paper-text); font-weight: 700; line-height: 1;
  }
  .back-brand .main { display: block; font-size: 42px; letter-spacing: 4px; }
  .back-brand .sub { display: block; font-size: 12px; letter-spacing: 0.8px; margin-top: 6px; }
</style>
</head>
<body>
<main class="stage">
  <section class="card card--front" aria-label="Card front">
    <div class="brand">
      <span class="brand__dot"></span>
      <span class="brand__name">
        <span class="main">QUARROW</span>
        <span class="sub">SIGNAL INSTRUMENTS</span>
      </span>
    </div>
    <div class="divider"></div>
    <div class="contact">
      <div class="contact__name">DORIN VASKEL</div>
      <div class="contact__title">President</div>
      <div class="contact__address">1820 Linden Cove Road<br>Port Aldis CA 90417</div>
      <div class="contact__line">
        <svg viewBox="0 0 12 12" aria-hidden="true"><path d="M2.5 1h2l1 3-1.3 1a6 6 0 0 0 2.8 2.8l1-1.3 3 1v2a1.5 1.5 0 0 1-1.5 1.5A9.5 9.5 0 0 1 1 2.5 1.5 1.5 0 0 1 2.5 1z"/></svg>
        555-014-2290
      </div>
      <div class="contact__line">
        <svg viewBox="0 0 12 12" aria-hidden="true"><path d="M1 3h10v6H1z M1 3l5 3.5L11 3" stroke="#fff" stroke-width="0.8"/></svg>
        d.vaskel@quarrow.com
      </div>
      <div class="contact__line">
        <svg viewBox="0 0 12 12" aria-hidden="true"><circle cx="6" cy="6" r="5"/></svg>
        www.quarrow.com
      </div>
    </div>
  </section>

  <section class="card card--back" aria-label="Card back">
    <div class="back-brand">
      <span class="main">QUARROW</span>
      <span class="sub">SIGNAL INSTRUMENTS</span>
    </div>
  </section>
</main>
</body>
</html>
```